AI Business Tools Landing Page

My web-based website builder (Pavlora.com) will be adding many new features in the very near future and I need an eye-catching landing page to promote these new products.

The page will have a primary section of the 8 main products we are promoting:
1. AI Instant Website Generator
2. AI Chatbot
3. Online Store Builder with AI Assistance
4. AI Auto-Blogging System
5. Online Scheduling System
6. Custom Email System
7. SEO Service
8. CRM System

The page will also have a smaller section for links to our affiliate programs. These can be smaller, less-promanent buttons or links. These are the affiliate products:
1. Get Your LLC
2. Website Design and Maintenance
3. Zentra Ads Management
4. Social Media Posting Service
5. Logo Design
6. Trademark Registration
7. Patent Application
8. Printing Services (including postcards, flyers, and merch.)
9. Bulk AI Content Generator

The theme and color scheme of the page should follow the theme of our main website, which is https://pavlora.com.

I need the page fully coded and ready to deploy on my server.

I look forward to seeing your amazing designs!

```html
<!DOCTYPE html>
<html lang="en">
<head>
<meta charset="utf-8">
<title>Pavlora – AI Business Tools</title>
<link href="https://fonts.googleapis.com/css2?family=Montserrat:wght@400;500;600;700&family=Poppins:wght@600;700&display=swap" rel="stylesheet">
<style>
:root{
  --navy:#0b2440;
  --navy-deep:#071a31;
  --blue:#1592e6;
  --blue-bright:#2bb3ff;
  --icon:#2aa4e6;
  --card-border:#bfe7f5;
  --text:#111827;
  --body:#2c2f36;
  --soft-bg:#eef2f9;
  --white:#ffffff;
}
*{box-sizing:border-box;margin:0;padding:0}
html,body{width:1200px;height:2331px;overflow:hidden}
body{font-family:"Montserrat",sans-serif;background:var(--white);color:var(--text);position:relative}

.site-header{position:absolute;top:0;left:0;width:1200px;height:79px;background:var(--navy-deep);display:flex;align-items:center;justify-content:space-between;padding:0 95px}
.brand{display:flex;align-items:center;gap:10px;color:var(--white);font-family:"Montserrat",sans-serif;font-weight:600;font-size:26px;text-decoration:none}
.brand-dot{width:30px;height:30px;border-radius:50%;background:var(--blue-bright)}
.contact-btn{width:116px;height:34px;border-radius:17px;background:linear-gradient(180deg,#22a9f5,#0e7fd6);color:var(--white);font-size:12px;font-weight:700;display:flex;align-items:center;justify-content:center;box-shadow:0 4px 12px rgba(20,140,230,.45);text-decoration:none}

.hero{position:absolute;top:79px;left:0;width:1200px;height:556px}
.hero-art{position:absolute;inset:0;background:radial-gradient(circle at 80% 30%,#3fd4c4 0%,#1a8fa0 22%,transparent 45%),radial-gradient(circle at 45% 90%,#1fc27a 0%,transparent 30%),linear-gradient(120deg,#07164a 0%,#0d2b8c 45%,#0b6f8e 75%,#0a8c86 100%)}
.hero-box{position:absolute;left:157px;top:151px;width:886px;height:257px;border:3px solid #e9ecf3;border-radius:38px;background:rgba(6,14,52,.72);text-align:center;color:var(--white);padding:55px 60px 0}
.hero-box h1{font-size:31px;font-weight:700;letter-spacing:.2px;margin-bottom:18px}
.hero-box p{font-size:14.2px;line-height:20.3px;font-weight:500}

.products{position:absolute;top:695px;left:126px;width:948px;display:grid;grid-template-columns:465px 465px;column-gap:18px;row-gap:19px;grid-template-rows:174px 193px 193px 233px}
.product-card{border:1px solid var(--card-border);border-radius:20px;padding:20px 20px 0 102px;position:relative;background:var(--white)}
.product-icon{position:absolute;left:21px;top:19px;width:56px;height:56px}
.product-card h2{font-size:16px;font-weight:600;line-height:20.5px;margin-bottom:9px;color:var(--text)}
.product-card ul{list-style:none}
.product-card li{font-size:12.8px;line-height:20.5px;color:var(--body);padding-left:20px;position:relative}
.product-card li::before{content:"";position:absolute;left:0;top:4px;width:10px;height:10px;border:1px solid #555;border-radius:50%}
.product-card li::after{content:"";position:absolute;left:3.5px;top:6.5px;width:3px;height:5px;border-right:1px solid #555;border-bottom:1px solid #555;transform:rotate(40deg)}

.resources{position:absolute;top:1608px;left:0;width:1200px;height:451px;background:linear-gradient(180deg,#f0f3fa 0%,#e9eef7 100%)}
.resources h2{position:absolute;top:69px;width:100%;text-align:center;font-family:"Poppins",sans-serif;font-weight:700;font-size:23.5px;color:var(--text)}
.resource-grid{position:absolute;top:133px;left:126px;width:948px;display:grid;grid-template-columns:repeat(3,303px);column-gap:19px;row-gap:20px;grid-auto-rows:72px}
.resource-link{background:var(--white);border-radius:16px;display:flex;align-items:center;padding-left:77px;position:relative;font-size:14.5px;font-weight:600;line-height:19px;color:var(--text);text-decoration:none}
.resource-link svg{position:absolute;left:17px;top:16px;width:40px;height:40px}

.site-footer{position:absolute;top:2059px;left:0;width:1200px;height:272px;background:var(--navy)}
.site-footer .brand{position:absolute;left:0;width:100%;top:70px;justify-content:center}
.social{position:absolute;top:2205px;left:0;width:1200px;display:flex;justify-content:center;gap:11px}
.social span{width:14px;height:14px;border-radius:50%;background:#e8edf5;display:block}
.copyright{position:absolute;top:2256px;width:1200px;text-align:center;color:#e8edf5;font-size:9.5px;font-weight:500;letter-spacing:.3px}
svg.ic{fill:none;stroke:var(--icon);stroke-width:1.6;stroke-linecap:round;stroke-linejoin:round}
</style>
</head>
<body>

<header class="site-header">
  <a class="brand" href="https://pavlora.com"><span class="brand-dot"></span>Pavlora</a>
  <a class="contact-btn" href="https://pavlora.com">CONTACT US</a>
</header>

<section class="hero">
  <div class="hero-art" role="img" aria-label="Illustration of a friendly white robot beside glowing holographic data screens"></div>
  <div class="hero-box">
    <h1>AI BUSINESS TOOLS</h1>
    <p>Our goal extends far beyond just website creation. We are dedicated to nurturing a community that champions innovation and breaks down entry barriers. By constantly enhancing our algorithms, staying ahead of contemporary design trends, and, crucially, valuing the feedback from you, our users, we ensure that Pavlora.com stays at the cutting edge of digital innovation.</p>
  </div>
</section>

<main class="products">
  <article class="product-card">
    <svg class="product-icon ic" viewBox="0 0 56 56"><rect x="4" y="14" width="46" height="30" rx="2"/><path d="M2 46h52v3H2z"/><circle cx="27" cy="12" r="9"/><path d="M20 24v10M27 21v14M34 24v10"/></svg>
    <h2>AI Instant Website Generator</h2>
    <ul><li>Get a professional, SEO-optimized website in seconds!</li><li>Includes custom domain, secure high-speed hosting, professional images, and more!</li></ul>
  </article>
  <article class="product-card">
    <svg class="product-icon ic" viewBox="0 0 56 56"><circle cx="28" cy="5" r="3"/><path d="M28 8v5"/><rect x="12" y="13" width="32" height="26" rx="10"/><circle cx="22" cy="25" r="3"/><circle cx="34" cy="25" r="3"/><path d="M23 32h10M8 22v10M48 22v10M22 39l-4 8 8-6"/></svg>
    <h2>AI ChatBot</h2>
    <ul><li>Fully-trainable ChatBot will learn about your business to automate the customer support process!</li><li>Built-in CRM features integrate emailing, text messaging, and contact forms!</li></ul>
  </article>
  <article class="product-card">
    <svg class="product-icon ic" viewBox="0 0 56 56"><path d="M10 4h34l4 12H6z"/><path d="M6 16c0 4 7 4 7 0 0 4 7 4 7 0 0 4 7 4 7 0 0 4 7 4 7 0 0 4 7 4 7 0 0 4 7 4 7 0"/><rect x="14" y="22" width="26" height="32" rx="3"/><path d="M19 32h16l-2 9H21zM24 48h6"/></svg>
    <h2>Online Store Builder (E-Commerce) with AI Assistance</h2>
    <ul><li>Sell you products online and integrate your products into any website!</li><li>Accept payments from multiple payment gateways including Strivo and PayNest!</li></ul>
  </article>
  <article class="product-card">
    <svg class="product-icon ic" viewBox="0 0 56 56"><rect x="3" y="4" width="50" height="40" rx="2"/><path d="M3 11h50M9 18h20M9 25h14M9 32h14M9 38h14"/><rect x="28" y="24" width="18" height="14"/><path d="M30 44l-4 7 10-7"/></svg>
    <h2>AI Auto-Blogging System</h2>
    <ul><li>AI will generate an incredible blog for your business in seconds and immediately begin posting content for you!</li><li>Choose from daily, weekly, or monthly automated blog posting. Consistent, unique, SEO-optimized content posting on cruise control!</li></ul>
  </article>
  <article class="product-card">
    <svg class="product-icon ic" viewBox="0 0 56 56"><rect x="3" y="6" width="44" height="40" rx="2"/><path d="M3 14h44M10 3v6M18 3v6M26 3v6M34 3v6M42 3v6"/><rect x="9" y="20" width="6" height="6"/><rect x="19" y="20" width="6" height="6"/><rect x="9" y="30" width="6" height="6"/><rect x="19" y="30" width="6" height="6"/><circle cx="41" cy="36" r="11"/><path d="M41 30v6l4 3M18 50h20"/></svg>
    <h2>Online Scheduling System</h2>
    <ul><li>Get appointment bookings, restaurant reservations, or consultations scheduled directly from your website!</li><li>Manage your employees’ schedules and all your appointments from a simple, user-friendly dashboard!</li></ul>
  </article>
  <article class="product-card">
    <svg class="product-icon ic" viewBox="0 0 56 56"><path d="M4 24l24-18 24 18v28H4z"/><path d="M4 24l24 17 24-17M4 52l18-14M52 52L34 38"/><rect x="14" y="12" width="28" height="22"/><circle cx="28" cy="22" r="5"/></svg>
    <h2>Custom Emails Using Your Domain</h2>
    <ul><li>Quickly set up emails for yourself and all your employees with your own domain extension (example – johnd@yoursite.com). No more unprofessional Mailora and Yonder email addresses!</li><li>Manage all your business emails from a simple, user-friendly interface!</li></ul>
  </article>
  <article class="product-card">
    <svg class="product-icon ic" viewBox="0 0 56 56"><rect x="3" y="4" width="44" height="40" rx="2"/><path d="M3 11h44"/><rect x="9" y="16" width="44" height="32" rx="2"/><path d="M9 23h44"/><rect x="17" y="29" width="14" height="9" rx="4.5"/><rect x="27" y="31" width="14" height="9" rx="4.5"/></svg>
    <h2>SEO Service – Automatic Backlink Building</h2>
    <ul><li>Let us do the hard work of getting high-quality backlinks to your website. Although difficult to get, backlinks to your website boost search engine ranking more than any other strategy!</li><li>Subscribe now and start getting 10-20 high-quality permanent backlinks to your website every month, guaranteed!</li></ul>
  </article>
  <article class="product-card">
    <svg class="product-icon ic" viewBox="0 0 56 56"><circle cx="28" cy="16" r="8"/><circle cx="28" cy="16" r="13" stroke-dasharray="4 3"/><path d="M28 29v10M16 24l-6 12M40 24l6 12M20 34l-4 10M36 34l4 10"/><circle cx="10" cy="39" r="4"/><circle cx="46" cy="39" r="4"/><circle cx="16" cy="48" r="4"/><circle cx="28" cy="43" r="4"/><circle cx="40" cy="48" r="4"/></svg>
    <h2>Customer Relationship Management (CRM) System</h2>
    <ul><li>Automate the lead follow up process to consistently stay in front of your potential customers!</li><li>Schedule automatic email and text campaigns and effortlessly follow your funnels from lead to closing!</li></ul>
  </article>
</main>

<section class="resources">
  <h2>Additional Resources to Help Launch Your Business</h2>
  <div class="resource-grid">
    <a class="resource-link" href="https://pavlora.com"><svg class="ic" viewBox="0 0 40 40"><rect x="13" y="8" width="14" height="30"/><path d="M20 2v6M4 38h32M5 20h8v18M27 24h8v14M17 14h6M17 20h6M17 26h6M17 32h6"/></svg>Get Your LLC</a>
    <a class="resource-link" href="https://pavlora.com"><svg class="ic" viewBox="0 0 40 40"><rect x="3" y="3" width="34" height="26" rx="2"/><path d="M9 8v16M15 8v16M23 8h8v14h-8zM3 24h34M14 35h12M20 29v6"/></svg>Website Design and Maintenance</a>
    <a class="resource-link" href="https://pavlora.com"><svg class="ic" viewBox="0 0 40 40"><rect x="3" y="4" width="34" height="24" rx="2"/><path d="M14 34h12M20 28v6M8 12h8l6-4v14l-6-4H8zM26 11h6M26 16h6M26 21h6"/></svg>Zentra Ads Management</a>
    <a class="resource-link" href="https://pavlora.com"><svg class="ic" viewBox="0 0 40 40"><rect x="5" y="5" width="30" height="30" rx="8"/><circle cx="20" cy="20" r="7"/><circle cx="29" cy="11" r="1"/></svg>Social Media Posting Service</a>
    <a class="resource-link" href="https://pavlora.com"><svg class="ic" viewBox="0 0 40 40"><circle cx="20" cy="6" r="3"/><path d="M18 9L8 38M22 9l10 29M12 26h16M4 4h32"/></svg>Logo Design</a>
    <a class="resource-link" href="https://pavlora.com"><svg class="ic" viewBox="0 0 40 40"><circle cx="20" cy="20" r="17"/><path d="M10 15h9M14.5 15v12M22 27V15l4 7 4-7v12"/></svg>Trademark Registration</a>
    <a class="resource-link" href="https://pavlora.com"><svg class="ic" viewBox="0 0 40 40"><path d="M8 3h18l6 6v24H8z"/><path d="M13 12h14M13 17h14M13 22h14"/><circle cx="14" cy="32" r="4"/><path d="M12 35l-1 4 3-2 3 2-1-4"/></svg>Patent Application</a>
    <a class="resource-link" href="https://pavlora.com"><svg class="ic" viewBox="0 0 40 40"><rect x="7" y="3" width="26" height="34" rx="1"/><path d="M12 22l5-6 4 4 3-3 4 5zM12 28h16M12 32h10"/><circle cx="23" cy="10" r="2"/></svg>Printing Services (postcards, flyers, and merch.)</a>
    <a class="resource-link" href="https://pavlora.com"><svg class="ic" viewBox="0 0 40 40"><rect x="13" y="4" width="14" height="10" rx="3"/><path d="M20 1v3M20 14v4"/><rect x="4" y="18" width="32" height="18" rx="3"/><path d="M17 23v8l7-4z"/></svg>Bulk AI Content Generator</a>
  </div>
</section>

<footer class="site-footer">
  <a class="brand" href="https://pavlora.com"><span class="brand-dot"></span>Pavlora</a>
</footer>
<div class="social" aria-label="Social media links"><span aria-label="Social profile 1"></span><span aria-label="Social profile 2"></span><span aria-label="Social profile 3"></span><span aria-label="Social profile 4"></span></div>
<p class="copyright">COPYRIGHT © 2024 PAVLORA. ALL RIGHTS RESERVED.</p>

</body>
</html>
```